Business Card Design for a Personal Trainer

I need a business card design for my job as a personal trainer. It should have a unique, modern and exclusive design. On the front there should be only my logo with my name and my job. 0162/3819204 Tobias Lendhart Wiesengrundweg 14 80417 Munich Germany The most important contact information is the web adress. it can be bigger than the rest, but its not necessary. The card should be 8,5cmx5,5cm big. Font: Roboto. Colors: black, white, gray, 56c1ff.

```html
<!DOCTYPE html>
<html lang="de">
<head>
<meta charset="utf-8">
<title>Tobias Lendhart – Personal Trainer Visitenkarte</title>
<link rel="stylesheet" href="https://fonts.googleapis.com/css2?family=Roboto:ital,wght@0,400;0,500;0,700;1,700&display=swap">
<style>
  :root {
    --bg: #111111;
    --card: #2c2c2c;
    --white: #ffffff;
    --text-soft: #eaeaea;
    --gray: #a9a9a9;
    --icon-ring: #d9d9d9;
    --icon-fill: #3a3a3a;
    --photo-dark: #1f1f1f;
    --photo-mid: #5a5a5a;
  }
  * { box-sizing: border-box; margin: 0; padding: 0; }
  html, body {
    width: 1189px; height: 1200px; overflow: hidden;
    background: var(--bg);
    font-family: "Roboto", Arial, sans-serif;
  }
  .canvas { position: relative; width: 1189px; height: 1200px; }
  .card {
    position: absolute; left: 218px; width: 752px; height: 486px;
    background: var(--card);
    box-shadow: 0 6px 18px rgba(0,0,0,.55);
    overflow: hidden;
  }
  .card--front { top: 76px; }
  .card--back { top: 605px; }

  .brand {
    position: absolute; left: 0; right: 0;
    text-align: center; color: var(--white);
    font-weight: 700; font-size: 44px; letter-spacing: 6px; line-height: 1;
  }
  .lockup { position: absolute; width: 390px; text-align: center; }
  .lockup__name {
    color: var(--white); font-weight: 400; font-size: 38px;
    letter-spacing: 1px; line-height: 1; white-space: nowrap;
  }
  .lockup__role {
    display: flex; align-items: center; gap: 8px; margin-top: 8px;
    color: var(--text-soft); font-size: 14px; letter-spacing: 4px;
    white-space: nowrap;
  }
  .lockup__role::before, .lockup__role::after {
    content: ""; flex: 1; height: 1px; background: var(--text-soft);
  }

  .card--front .brand { top: 180px; }
  .card--front .lockup { left: 181px; top: 282px; }

  .photo {
    position: absolute; left: 24px; top: 48px; width: 330px; bottom: 0;
    background: radial-gradient(ellipse at 50% 35%, var(--photo-mid), var(--photo-dark) 75%);
    border-radius: 140px 140px 0 0;
  }
  .card--back .brand { left: 364px; right: 8px; top: 82px; }
  .card--back .lockup { left: 365px; top: 176px; }

  .contact {
    position: absolute; left: 380px; width: 310px;
    text-align: center; color: var(--text-soft);
  }
  .icon {
    display: block; margin: 0 auto; width: 32px; height: 32px;
  }
  .contact--phone { top: 255px; }
  .contact--mail { top: 341px; }
  .contact__text { font-size: 21px; margin-top: 6px; letter-spacing: .5px; }
  .divider {
    position: absolute; left: 396px; top: 328px; width: 250px; height: 1px;
    background: linear-gradient(90deg, transparent, var(--gray), transparent);
  }
  .website {
    position: absolute; left: 360px; width: 350px; top: 424px;
    text-align: center; font-weight: 700; font-style: italic;
    font-size: 20px; letter-spacing: 2px; color: var(--white);
  }
  .website__domain { color: var(--gray); }
</style>
</head>
<body>
<main class="canvas">
  <section class="card card--front" aria-label="Vorderseite">
    <div class="brand">LENDHART</div>
    <div class="lockup">
      <p class="lockup__name">TOBIAS LENDHART</p>
      <p class="lockup__role">PERSONAL TRAINER</p>
    </div>
  </section>

  <section class="card card--back" aria-label="Rückseite">
    <div class="photo" role="img" aria-label="Schwarzweiß-Porträt des Trainers mit verschränkten Armen im Sportshirt"></div>
    <div class="brand">LENDHART</div>
    <div class="lockup">
      <p class="lockup__name">TOBIAS LENDHART</p>
      <p class="lockup__role">PERSONAL TRAINER</p>
    </div>

    <div class="contact contact--phone">
      <svg class="icon" viewBox="0 0 32 32" aria-hidden="true">
        <circle cx="16" cy="16" r="15" fill="var(--icon-ring)"/>
        <circle cx="16" cy="16" r="11" fill="var(--white)"/>
        <path d="M10 12c0-2 12-2 12 0v2h-3v-1.5h-6V14h-3z M11 15h10l1 6H10z" fill="var(--icon-fill)"/>
      </svg>
      <p class="contact__text">0162/3819204</p>
    </div>
    <div class="divider"></div>
    <div class="contact contact--mail">
      <svg class="icon" viewBox="0 0 32 32" aria-hidden="true">
        <circle cx="16" cy="16" r="15" fill="var(--icon-ring)"/>
        <circle cx="16" cy="16" r="11" fill="var(--white)"/>
        <rect x="9" y="11" width="14" height="10" rx="1" fill="none" stroke="var(--icon-fill)" stroke-width="1.6"/>
        <path d="M9 11l7 6 7-6" fill="none" stroke="var(--icon-fill)" stroke-width="1.6"/>
      </svg>
      <p class="contact__text">Info@yourgmail.com</p>
    </div>
    <p class="website">www.<span class="website__domain">YOURWEBSITE</span>.com</p>
  </section>
</main>
</body>
</html>
```